Business card for Luxury Portable Restroom Trailer company

We are a Luxury Portable Restroom Trailer Company Called FALCRIDGE HIRES. Based in Orange County California. We provide portable restroom trailers for events, such as, Weddings, Concerts, Charity events, Sporting events, Tournaments, Corporate events, ect. We rent and Sell the Luxury restrooms. Our colors are white, grey, and Orange. As you will see in the logo we uploaded.
There are 2 people in the company so the names and titles will change for the 3 people but card will remain the same. Here is the information for each Person: Dwight Penner CFO 555 318-0476
next Person: Leon Marchetti VP 555 318-0476
Next Person: Owen Marchetti CEO 555 318-0476
Information to include on the card: Luxury Restroom Trailers Rental and Sales. Weddings, Concerts, Charity, Sporting and Corp. Events.

```html
<!DOCTYPE html>
<html lang="en">
<head>
<meta charset="utf-8">
<title>Falcridge Hires – Business Card</title>
<link rel="stylesheet" href="https://fonts.googleapis.com/css2?family=Montserrat:wght@400;500;700;800&family=Open+Sans:wght@400;600&display=swap">
<style>
  :root {
    --orange: #e0601f;
    --orange-light: #e88a5c;
    --grey-dark: #58595b;
    --grey-mid: #6d6e70;
    --card-white: #ffffff;
    --card-mist: #f0f0f0;
    --backdrop: #d9d9d9;
  }
  * { box-sizing: border-box; margin: 0; padding: 0; }
  html, body { width: 1200px; height: 1200px; overflow: hidden; }
  body {
    background: var(--backdrop);
    font-family: "Montserrat", sans-serif;
    position: relative;
  }
  .card {
    position: absolute;
    left: 250px;
    width: 700px;
    height: 400px;
    border-radius: 22px;
    overflow: hidden;
    box-shadow: 0 10px 24px rgba(0,0,0,0.18);
  }
  /* Front */
  .card-front { top: 150px; background: var(--card-white); }
  .brand {
    position: absolute;
    top: 110px; left: 0; right: 0;
    display: flex; align-items: center; justify-content: center; gap: 18px;
  }
  .brand-square { width: 34px; height: 34px; background: var(--orange); }
  .brand-name {
    font-family: "Montserrat", sans-serif;
    font-weight: 800;
    font-size: 52px;
    letter-spacing: 1px;
    color: var(--orange);
  }
  .services {
    position: absolute;
    top: 270px; left: 0; right: 0;
    text-align: center;
    font-family: "Open Sans", sans-serif;
    font-size: 19px;
    line-height: 1.45;
    color: var(--orange);
  }
  /* Back */
  .card-back { top: 640px; background: var(--card-mist); }
  .back-brand {
    position: absolute; top: 40px; right: 44px;
    display: flex; align-items: center; gap: 10px;
  }
  .back-brand .brand-square { width: 18px; height: 18px; background: var(--grey-dark); }
  .back-brand .brand-name { font-size: 26px; color: var(--grey-dark); }
  .person { position: absolute; top: 88px; left: 60px; }
  .person-name { font-weight: 700; font-size: 34px; color: var(--orange); }
  .person-title { font-weight: 400; font-size: 18px; color: var(--grey-mid); margin-top: 4px; margin-left: 14px; }
  .contact-band {
    position: absolute; left: 0; right: 0; bottom: 0; height: 215px;
    background: linear-gradient(90deg, var(--orange-light) 0%, var(--orange) 45%, var(--orange) 100%);
  }
  .emblem-area {
    position: absolute; right: 0; bottom: 0; width: 300px; height: 300px;
    background: var(--orange);
    border-top-left-radius: 220px 160px;
  }
  .contact { position: absolute; left: 90px; top: 28px; color: #fff; font-size: 18px; }
  .address { line-height: 1.4; margin-bottom: 16px; }
  .contact-line { display: flex; align-items: center; gap: 12px; line-height: 1.55; margin-left: 14px; }
  .contact-line svg { width: 16px; height: 16px; flex: none; }
</style>
</head>
<body>

<section class="card card-front">
  <div class="brand">
    <span class="brand-square"></span>
    <span class="brand-name">FALCRIDGE HIRES</span>
  </div>
  <p class="services">
    Luxury Restroom | Trailers Rental and Sales | Weddings |<br>
    Concerts | Charity | Sporting and Corp. Events
  </p>
</section>

<section class="card card-back">
  <div class="back-brand">
    <span class="brand-square"></span>
    <span class="brand-name">FALCRIDGE HIRES</span>
  </div>
  <div class="person">
    <h1 class="person-name">Dwight Penner</h1>
    <p class="person-title">CFO</p>
  </div>
  <div class="contact-band">
    <div class="contact">
      <p class="address">4710 Alder Crest Way<br>Tustin Ridge California 92780</p>
      <p class="contact-line">
        <svg viewBox="0 0 16 16" aria-hidden="true"><path fill="#fff" d="M3.5 1.5l2.5 3-1.5 1.5c.8 1.8 2.2 3.2 4 4l1.5-1.5 3 2.5-1.5 2.5C6.5 13 3 9.5 1 4z"/></svg>
        555 318-0476
      </p>
      <p class="contact-line">
        <svg viewBox="0 0 16 16" aria-hidden="true"><rect x="1" y="3" width="14" height="10" fill="#fff"/><path d="M1 3l7 6 7-6" fill="none" stroke="#e0601f" stroke-width="1.4"/></svg>
        info@falcridgehires.com
      </p>
      <p class="contact-line">
        <svg viewBox="0 0 16 16" aria-hidden="true"><circle cx="8" cy="8" r="6.5" fill="none" stroke="#fff" stroke-width="1.5"/><path d="M1.5 8h13M8 1.5c-3 3.5-3 9.5 0 13M8 1.5c3 3.5 3 9.5 0 13" fill="none" stroke="#fff" stroke-width="1.2"/></svg>
        www.falcridgehires.com
      </p>
    </div>
  </div>
  <div class="emblem-area" role="img" aria-label="Large brand emblem decoration in white line on orange"></div>
</section>

</body>
</html>
```